Initial website for sport tech startup

We are currently in the R&D phases of our new product. It’s a headband to prevent concussion in the soccer market initially.

We have 2 products, one that’s basic aimed at the youth market and the other more technology driven that’s aimed at the academies and professional market.

Initially the product will launch in the UK

Target Market(s)

Youth soccer players and parents in UK, Soccer Clubs, Federations.

Industry/Entity Type

Sporting Good

Coding

Coded - Design and coding required

Number of Pages Required

5+ page

Requirements
Must have
• Professional style that can be adapted and changed over the coming months.
Nice to have
• Ecommerce ability in the future.

```html
<!DOCTYPE html>
<html lang="en">
<head>
<meta charset="utf-8">
<title>Helmora – Head protection for sport</title>
<link href="https://fonts.googleapis.com/css2?family=Raleway:wght@500;600;700&family=Open+Sans:wght@400;600&display=swap" rel="stylesheet">
<style>
:root{
  --brand:#1a6ea8;
  --brand-dark:#1b4d99;
  --footer:#0b4a78;
  --ink:#2b2b2b;
  --muted:#555;
  --white:#ffffff;
}
*{margin:0;padding:0;box-sizing:border-box}
html,body{width:1200px;height:3597px;overflow:hidden;background:var(--white)}
body{position:relative;font-family:"Open Sans",Arial,sans-serif;color:var(--ink)}
.abs{position:absolute}
.heading{font-family:"Raleway",Arial,sans-serif;font-weight:700}

/* header */
.site-header{left:0;top:0;width:1200px;height:102px;background:var(--white)}
.logo-text{font-family:"Raleway",Arial,sans-serif;font-weight:600;letter-spacing:2px;color:var(--brand)}
.site-header .logo-text{left:113px;top:22px;font-size:42px;line-height:50px}
.main-nav{left:424px;top:36px;display:flex;gap:30px;font-family:"Raleway",Arial,sans-serif;font-weight:500;font-size:17px}
.main-nav span{color:#222}
.main-nav .active{color:var(--brand)}

/* hero */
.hero{left:0;top:102px;width:1200px;height:558px;background:linear-gradient(135deg,#2f3a2c 0%,#4d6a4a 35%,#a9b4b8 55%,#3c4b3a 80%,#26301f 100%)}
.hero-box{left:233px;top:244px;width:734px;height:274px;background:rgba(40,40,40,.55);text-align:center;color:var(--white)}
.hero-title{margin-top:36px;font-size:64px;line-height:70px;text-shadow:0 2px 6px rgba(0,0,0,.4)}
.hero-sub{margin:16px auto 0;width:680px;font-family:"Raleway",Arial,sans-serif;font-weight:700;font-size:25px;line-height:36px;text-shadow:0 2px 4px rgba(0,0,0,.5)}
.btn{display:inline-block;border-radius:24px;color:var(--white);font-family:"Open Sans",Arial,sans-serif;font-weight:600;font-size:18px;text-align:center}
.hero-box .btn{margin-top:24px;background:var(--brand-dark);padding:0 16px;line-height:42px}
.dots{left:588px;top:627px;display:flex;gap:8px}
.dots i{display:block;width:10px;height:10px;border-radius:50%;background:rgba(255,255,255,.5)}
.dots i:first-child{background:var(--brand)}

/* mission */
.section-title{left:0;width:1200px;text-align:center;font-size:40px;line-height:46px;color:var(--ink)}
.section-title em{font-style:normal;color:var(--brand)}
.mission-title{top:763px}
.mission-text{left:155px;top:840px;width:890px;text-align:center;font-size:16px;line-height:32.5px;color:var(--muted)}
.mission-actions{top:1038px;left:439px;display:flex;gap:36px}
.mission-actions .btn{line-height:44px;padding:0 20px}
.btn-blue{background:var(--brand-dark)}
.btn-dark{background:#222}

/* market */
.market{left:0;top:1131px;width:1200px;height:597px}
.market-title{top:1245px;color:var(--white)}
.stat{width:300px;text-align:center;color:var(--white)}
.stat svg{display:block;margin:0 auto}
.stat p{margin-top:38px;font-family:Arial,"Raleway",sans-serif;font-size:20px;line-height:34px}

/* product */
.product-title{left:109px;top:1800px;font-size:40px;line-height:46px;color:var(--brand)}
.product-text{left:109px;top:1872px;width:480px;font-size:15.5px;line-height:33.5px;color:var(--muted)}
.product-btn{left:109px;top:2165px;background:var(--brand-dark);line-height:45px;width:144px}
.product-visual{left:615px;top:1799px;width:550px;height:331px;border-radius:28px;background:linear-gradient(160deg,#5c616a 0%,#464a52 55%,#3a3d44 100%)}

/* team */
.team{left:0;top:2285px;width:1200px;height:540px;background:linear-gradient(160deg,#3a3a3a 0%,#1d1d1d 55%,#2a2f26 100%)}
.team-title{top:2343px;color:var(--white)}
.card{top:2561px;width:280px;height:205px;background:var(--white);clip-path:polygon(0 0,100% 0,100% 100%,0 95%);text-align:center}
.card h3{margin-top:94px;font-family:Arial,"Raleway",sans-serif;font-weight:700;font-size:19px;color:#333}
.card .role{margin-top:8px;font-family:Arial,sans-serif;font-size:14px;color:#888}
.card .social{margin-top:12px;display:flex;justify-content:center;gap:10px}
.social i{display:block;width:24px;height:24px;border:1.5px solid var(--brand-dark);border-radius:50%}
.avatar{top:2454px;width:168px;height:168px;border-radius:50%;border:4px solid var(--white)}

/* partners */
.partners{left:0;top:2945px;width:1200px;height:60px}

/* footer */
.site-footer{left:0;top:3104px;width:1200px;height:493px;background:var(--footer)}
.footer-logo{left:479px;top:3167px;width:242px;height:56px;border:3px solid var(--white);text-align:center}
.footer-logo .logo-text{color:var(--white);font-size:38px;line-height:50px}
.footer-nav{left:0;top:3261px;width:1200px;display:flex;justify-content:center;gap:30px;font-family:"Raleway",Arial,sans-serif;font-weight:600;font-size:17px;color:var(--white)}
.contact-icon{width:52px;height:52px;border-radius:50%;background:var(--white)}
.contact-text{font-size:17px;line-height:31px;color:var(--white)}
.divider{width:1px;height:76px;background:rgba(255,255,255,.6)}
.legal{left:0;top:3472px;width:1200px;text-align:center;font-size:11px;color:var(--white)}
.footer-social{left:523px;top:3518px;display:flex;gap:20px}
.footer-social i{display:block;width:38px;height:38px;border:1.5px solid var(--white);border-radius:50%}
</style>
</head>
<body>

<header class="site-header abs">
  <div class="logo-text abs">HELMORA</div>
  <nav class="main-nav abs">
    <span class="active">HOME</span><span>ABOUT US</span><span>MISSION</span><span>PRODUCT</span><span>OUR TEAM</span><span>CONTACT US</span>
  </nav>
</header>

<section class="hero abs" role="img" aria-label="Football match photo: players tending to an injured player on the pitch"></section>
<div class="hero-box abs">
  <h1 class="hero-title heading">HELMORA</h1>
  <p class="hero-sub">Neque porro quisquam est qui dolorem ipsum quia dolor sit amet, consectetur, adipisci velit.</p>
  <span class="btn">GET STARTED</span>
</div>
<div class="dots abs"><i></i><i></i></div>

<h2 class="section-title mission-title heading abs">OUR <em>MISSSION</em></h2>
<p class="mission-text abs">Helmora is designing and developing head protectionproducts to reduce the likelihood of concussion when playing sports. Exploring and understanding medical insights, materialscience and composites research, current and former playersexperiences and governing bodies guidelines has allowedHelmora to develop the safety, style, form and functionrequirementsof a suitable product to bring to market in 2020.Soccer has no head protection product despite recent highprofile head injuries, concern over the long term damage of heading.</p>
<div class="mission-actions abs">
  <span class="btn btn-blue">READ MORE</span>
  <span class="btn btn-dark">CONTACT US</span>
</div>

<svg class="market abs" viewBox="0 0 1200 597" role="img" aria-label="Blue-tinted football match photo backdrop">
  <defs>
    <linearGradient id="bandFill" x1="0" y1="0" x2="1" y2="1">
      <stop offset="0" stop-color="#0d5590"/>
      <stop offset=".5" stop-color="#1866a3"/>
      <stop offset="1" stop-color="#0c5088"/>
    </linearGradient>
  </defs>
  <path d="M0,0 Q600,70 1200,0 L1200,597 Q600,495 0,597 Z" fill="url(#bandFill)"/>
</svg>
<h2 class="section-title market-title heading abs">THE MARKET TODAY</h2>
<div class="stat abs" style="left:96px;top:1375px">
  <svg width="152" height="152" role="img" aria-label="Icon of two young people"><circle cx="76" cy="76" r="69" fill="none" stroke="#fff" stroke-width="12"/></svg>
  <p>YOUTH SPEND £800PA<br>ON SPORTS KITS</p>
</div>
<div class="stat abs" style="left:462px;top:1375px">
  <svg width="152" height="152" role="img" aria-label="Icon of a football"><circle cx="76" cy="76" r="69" fill="none" stroke="#fff" stroke-width="12"/></svg>
  <p>UK SPORTSWEAR MARKET IS<br>FORECAST TO REACH £6.7BN</p>
</div>
<div class="stat abs" style="left:804px;top:1375px">
  <svg width="152" height="152" role="img" aria-label="Icon of money and coins"><circle cx="76" cy="76" r="69" fill="none" stroke="#fff" stroke-width="12"/></svg>
  <p>AV ADULT SPEND £700 PA<br>ON SPORTS KITS</p>
</div>

<h2 class="product-title heading abs">OUR PRODUCT</h2>
<p class="product-text abs">Our initial product will be simplistic in function and design to ensurewe get to market in 2020. Further versions of the product willincorporate data tracking technologies to enhance analytical streams available to players and clubs. Starting with soccer, followed by other markets such as netball and field hockey, where the same issues exist today. We will create a new sector of sports apparel that will serve all communities of sport and allow for new categories of sponsorship and branding.</p>
<span class="btn product-btn abs">READ MORE</span>
<div class="product-visual abs" role="img" aria-label="Illustration of the grey protective headband"></div>

<section class="team abs" role="img" aria-label="Dark photo of a football boot on a pitch"></section>
<h2 class="section-title team-title heading abs">OUR TEAM</h2>

<div class="card abs" style="left:128px">
  <h3>MARTIN KESSLER</h3><p class="role">Founder / CEO</p>
  <div class="social"><i></i><i></i><i></i></div>
</div>
<div class="avatar abs" style="left:167px;background:#b8574f" role="img" aria-label="Portrait photo of Martin Kessler"></div>

<div class="card abs" style="left:435px">
  <h3>FIONA DRAYCOTT</h3><p class="role">Co –Founder / COO</p>
  <div class="social"><i></i><i></i><i></i></div>
</div>
<div class="avatar abs" style="left:485px;background:#9a8f86" role="img" aria-label="Portrait photo of Fiona Draycott"></div>

<div class="card abs" style="left:749px">
  <h3>OWEN TALBRIGHT</h3><p class="role">CCO</p>
  <div class="social"><i></i><i></i><i></i></div>
</div>
<div class="avatar abs" style="left:794px;background:#c9c3bd" role="img" aria-label="Portrait photo of Owen Talbright"></div>

<svg class="partners abs" viewBox="0 0 1200 60" role="img" aria-label="Partner association badges">
  <rect x="147" y="18" width="120" height="26" rx="4" fill="#c8c8c8"/>
  <rect x="333" y="8" width="130" height="44" rx="4" fill="#bdbdbd"/>
  <circle cx="574" cy="30" r="20" fill="#a9b6d6"/>
  <rect x="681" y="10" width="100" height="40" rx="4" fill="#b9a6c9"/>
  <rect x="872" y="6" width="36" height="48" rx="6" fill="#c7cde0"/>
  <rect x="992" y="16" width="76" height="28" rx="3" fill="#b7c4dc"/>
</svg>

<footer class="site-footer abs"></footer>
<div class="footer-logo abs"><span class="logo-text">HELMORA</span></div>
<nav class="footer-nav abs"><span>HOME</span><span>ABOUT US</span><span>MISSION</span><span>PRODUCT</span><span>OUR TEAM</span><span>CONTACT US</span></nav>

<div class="contact-icon abs" style="left:131px;top:3352px">
  <svg width="52" height="52" viewBox="0 0 52 52"><path d="M26 14a8 8 0 0 0-8 8c0 6 8 15 8 15s8-9 8-15a8 8 0 0 0-8-8z" fill="var(--footer)"/><circle cx="26" cy="22" r="3" fill="#fff"/></svg>
</div>
<p class="contact-text abs" style="left:209px;top:3338px;width:210px">Neque porro quisquam estqudolorem,iconsectet uadipisci velit.</p>
<div class="divider abs" style="left:429px;top:3338px"></div>

<div class="contact-icon abs" style="left:471px;top:3339px">
  <svg width="52" height="52" viewBox="0 0 52 52"><path d="M19 14l5 6-3 4c2 4 5 7 9 9l4-3 6 5-3 4c-10 0-21-11-21-21z" fill="var(--footer)"/></svg>
</div>
<p class="contact-text abs" style="left:548px;top:3349px;font-size:20px">Tel:&nbsp; +44 20 7946 0321</p>
<div class="divider abs" style="left:756px;top:3338px"></div>

<div class="contact-icon abs" style="left:778px;top:3339px">
  <svg width="52" height="52" viewBox="0 0 52 52"><rect x="15" y="18" width="22" height="16" fill="var(--footer)"/><path d="M15 18l11 9 11-9" fill="none" stroke="#fff" stroke-width="2"/></svg>
</div>
<p class="contact-text abs" style="left:845px;top:3349px;font-size:22px">Email:hello@helmora.com</p>

<p class="legal abs">© 2020 All Rights Reserved | Privacy Policy | Terms and Conditions | Impressum</p>
<div class="footer-social abs"><i></i><i></i><i></i></div>

</body>
</html>
```